QVR business card

Need a business card for a company that provides instructional design and elearning development services. The website is here: http://quorvane.studio/

I'm attaching a current logo, as well as the old business card design. While I like to keep it clean, the old design is too simplistic for my liking. The only idea I want to reuse from the old design is placing industry jargon on the back of the card, just need a better way to present it. But if you have other ideas for the back--feel free to experiment.

Please use the colors complementary to the color we have on the website. Thank you!

```html
<!DOCTYPE html>
<html lang="en">
<head>
<meta charset="utf-8">
<title>QVR business card</title>
<link rel="stylesheet" href="https://fonts.googleapis.com/css2?family=Open+Sans:wght@400;600;700&display=swap">
<style>
  :root {
    --bg: #ece8e1;
    --teal: #10b0ad;
    --teal-dark: #15a3a1;
    --sand: #e6dba2;
    --white: #ffffff;
    --ink: #2b2b2b;
    --shadow: rgba(60, 45, 25, 0.22);
  }
  * { margin: 0; padding: 0; box-sizing: border-box; }
  html, body { width: 1200px; height: 900px; overflow: hidden; }
  body {
    background: var(--bg);
    font-family: "Open Sans", Arial, sans-serif;
    position: relative;
  }
  .card {
    position: absolute;
    width: 560px;
    height: 320px;
    border-radius: 4px;
    box-shadow: 0 10px 24px var(--shadow);
    overflow: hidden;
  }
  /* Back side */
  .card--back {
    left: 70px;
    top: 110px;
    background: linear-gradient(180deg, var(--teal) 0%, #5fc3b4 45%, var(--sand) 100%);
    color: var(--white);
  }
  .card--back .brand-name {
    position: absolute;
    left: 40px;
    top: 70px;
    font-size: 64px;
    font-weight: 700;
    letter-spacing: 2px;
    color: var(--white);
  }
  .services {
    position: absolute;
    left: 300px;
    top: 72px;
  }
  .services__title {
    font-size: 17px;
    font-weight: 600;
    letter-spacing: 0.5px;
    margin-bottom: 10px;
  }
  .services__list { list-style: none; }
  .services__item {
    display: flex;
    align-items: center;
    gap: 10px;
    font-size: 13px;
    line-height: 24px;
  }
  .services__bullet {
    width: 8px;
    height: 8px;
    background: var(--white);
    flex: none;
  }
  /* Front side */
  .card--front {
    left: 570px;
    top: 470px;
    background: var(--white);
  }
  .card--front .brand-name {
    position: absolute;
    left: 44px;
    top: 40px;
    font-size: 44px;
    font-weight: 700;
    letter-spacing: 2px;
    color: var(--teal-dark);
  }
  .contact {
    position: absolute;
    left: 300px;
    top: 150px;
    color: var(--ink);
  }
  .contact__name {
    font-size: 17px;
    font-weight: 700;
    color: var(--teal-dark);
    margin-bottom: 10px;
  }
  .contact__line {
    display: flex;
    align-items: center;
    gap: 8px;
    font-size: 13px;
    line-height: 22px;
  }
  .contact__icon { width: 12px; height: 12px; flex: none; }
</style>
</head>
<body>

<section class="card card--back" aria-label="Card back">
  <div class="brand-name">QVR</div>
  <div class="services">
    <h2 class="services__title">HOW CAN WE HELP?</h2>
    <ul class="services__list">
      <li class="services__item"><span class="services__bullet"></span>Mobile Learning Scorm</li>
      <li class="services__item"><span class="services__bullet"></span>Instructional Design Lms</li>
      <li class="services__item"><span class="services__bullet"></span>Moocs Elearning Html5</li>
      <li class="services__item"><span class="services__bullet"></span>Adult Learning Theory</li>
      <li class="services__item"><span class="services__bullet"></span>Gamification Classroom</li>
      <li class="services__item"><span class="services__bullet"></span>Xapi Blended Learning</li>
    </ul>
  </div>
</section>

<section class="card card--front" aria-label="Card front">
  <div class="brand-name">QVR</div>
  <div class="contact">
    <p class="contact__name">Marten Okafor</p>
    <p class="contact__line">
      <svg class="contact__icon" viewBox="0 0 12 12" aria-hidden="true"><path d="M2.5 1 L4.5 1 L5 3.5 L3.8 4.4 A7 7 0 0 0 7.6 8.2 L8.5 7 L11 7.5 L11 9.5 A1.5 1.5 0 0 1 9.5 11 A8.5 8.5 0 0 1 1 2.5 A1.5 1.5 0 0 1 2.5 1 Z" fill="#10b0ad"/></svg>
      555-014-7392
    </p>
    <p class="contact__line">
      <svg class="contact__icon" viewBox="0 0 12 12" aria-hidden="true"><rect x="0.5" y="2.5" width="11" height="7.5" fill="#10b0ad"/><path d="M0.5 2.5 L6 7 L11.5 2.5" fill="none" stroke="#fff" stroke-width="1"/></svg>
      mokafor@quorvane.studio
    </p>
    <p class="contact__line">
      <svg class="contact__icon" viewBox="0 0 12 12" aria-hidden="true"><circle cx="6" cy="6" r="5.5" fill="#10b0ad"/><path d="M0.5 6 H11.5 M6 0.5 C3 3 3 9 6 11.5 M6 0.5 C9 3 9 9 6 11.5" fill="none" stroke="#fff" stroke-width="0.8"/></svg>
      www.quorvane.studio
    </p>
  </div>
</section>

</body>
</html>
```